Lumavento business card

We need a modern business card - With our 4 colors - See web: www.lumavento.dk

I have attached logo and som old business Cards we have - Lets Make the new ones shine...:-) -

Industry/Entity Type

Business

Requirements
Must have
• the logo with lumavento only,

```html
<!DOCTYPE html>
<html lang="da">
<head>
<meta charset="utf-8">
<title>Lumavento – visitkort</title>
<link href="https://fonts.googleapis.com/css2?family=Source+Sans+3:wght@300;400;600&display=swap" rel="stylesheet">
<style>
  :root {
    --backdrop: #e9e9e9;
    --card: #ffffff;
    --lime: #8dc85a;
    --ink: #2b2b2b;
    --on-lime: #ffffff;
  }
  * { margin: 0; padding: 0; box-sizing: border-box; }
  html, body { width: 1105px; height: 1200px; overflow: hidden; }
  body {
    background: var(--backdrop);
    font-family: "Source Sans 3", sans-serif;
    position: relative;
  }
  .card {
    position: absolute;
    left: 196px;
    width: 720px;
    height: 412px;
    background: var(--card);
    border-radius: 22px;
    overflow: hidden;
    box-shadow: 0 4px 14px rgba(0,0,0,0.12);
  }
  .card--front { top: 146px; }
  .card--back { top: 602px; }

  .front__panel { position: absolute; inset: 0; }
  .front__panel path { fill: var(--lime); }

  .contact {
    position: absolute;
    right: 37px;
    top: 32px;
    text-align: right;
    color: var(--on-lime);
    font-weight: 400;
  }
  .contact__name { font-size: 26px; font-weight: 600; line-height: 1.1; }
  .contact__role { font-size: 19px; line-height: 1.25; margin-bottom: 16px; }
  .contact__address { font-size: 19px; line-height: 1.3; margin-bottom: 6px; }
  .contact__line {
    display: flex; justify-content: flex-end; align-items: center;
    gap: 12px; font-size: 19px; line-height: 28px;
  }
  .contact__line svg { width: 18px; height: 18px; fill: var(--on-lime); }

  .wordmark {
    position: absolute;
    font-weight: 400;
    letter-spacing: 3px;
    white-space: nowrap;
    transform: translateX(-50%);
  }
  .wordmark--front { left: 536px; top: 288px; font-size: 24px; color: var(--on-lime); }
  .rule { position: absolute; height: 3px; }
  .rule--front { left: 384px; width: 304px; top: 338px; background: var(--on-lime); }
  .tagline {
    position: absolute; font-size: 17px; white-space: nowrap; transform: translateX(-50%);
  }
  .tagline--front { left: 536px; top: 355px; color: var(--on-lime); }

  .wordmark--back { left: 360px; top: 236px; font-size: 25px; color: var(--ink); }
  .rule--back { left: 213px; width: 294px; top: 283px; height: 2px; background: var(--lime); }
  .tagline--back { left: 360px; top: 298px; color: var(--ink); }
</style>
</head>
<body>
  <section class="card card--front" aria-label="Visitkort forside">
    <svg class="front__panel" viewBox="0 0 720 412" preserveAspectRatio="none" aria-hidden="true">
      <path d="M398 0 H720 V412 H0 V330 C210 330 390 220 398 0 Z"/>
    </svg>
    <div class="contact">
      <p class="contact__name">Jonas Holmgaard</p>
      <p class="contact__role">Salgsdirektør</p>
      <p class="contact__address">Solsikkevej 14<br>2100 København Ø</p>
      <p class="contact__line">+45 31 42 77 18
        <svg viewBox="0 0 24 24" aria-hidden="true"><path d="M6.6 10.8a15 15 0 0 0 6.6 6.6l2.2-2.2a1 1 0 0 1 1-.25 11.4 11.4 0 0 0 3.6.57 1 1 0 0 1 1 1V20a1 1 0 0 1-1 1A17 17 0 0 1 3 4a1 1 0 0 1 1-1h3.5a1 1 0 0 1 1 1c0 1.250.2 2.45.57 3.57a1 1 0 0 1-.25 1z"/></svg></p>
      <p class="contact__line">+45 52 60 41 83
        <svg viewBox="0 0 24 24" aria-hidden="true"><path d="M6.6 10.8a15 15 0 0 0 6.6 6.6l2.2-2.2a1 1 0 0 1 1-.25 11.4 11.4 0 0 0 3.6.57 1 1 0 0 1 1 1V20a1 1 0 0 1-1 1A17 17 0 0 1 3 4a1 1 0 0 1 1-1h3.5a1 1 0 0 1 1 1c0 1.250.2 2.45.57 3.57a1 1 0 0 1-.25 1z"/></svg></p>
      <p class="contact__line">jh@lumavento.dk
        <svg viewBox="0 0 24 24" aria-hidden="true"><path d="M2 5h20v14H2z M2 5l10 8 10-8" fill="none" stroke="#fff" stroke-width="2"/></svg></p>
      <p class="contact__line">www.lumavento.dk
        <svg viewBox="0 0 24 24" aria-hidden="true"><circle cx="12" cy="12" r="10"/></svg></p>
    </div>
    <p class="wordmark wordmark--front">lumavento</p>
    <div class="rule rule--front"></div>
    <p class="tagline tagline--front">ideer der gror</p>
  </section>

  <section class="card card--back" aria-label="Visitkort bagside">
    <p class="wordmark wordmark--back">lumavento</p>
    <div class="rule rule--back"></div>
    <p class="tagline tagline--back">ideer der gror</p>
  </section>
</body>
</html>
```